Website for Dental Office - The Bright Arch Clinic

The bright arch clinic is a dental office offering cosmetic dentistry, general dentistry, and multi-specialty dental care all under one roof in our state-of-the-art cosmetic dental center. We are particularly striving to provide services that fit the need of the young generation. Thus, we hope to have a modern, professional concise website that represents our spirit.

*Should be able to switch from English to Chinese

6 sections besides homepage:
Home, Meet us, Services,
Patient Info, Cases&Reviews, Blog, Contact

The Services sections should contain multiple subsections such as cleaning and prevention, cosmetic dentistry, implant dentistry, removable dentures, etc...
The Patient Info section is also intended to contain several subsections such as
New Patient offer, accepted Insurance, patient portal, helpful tips, etc...

Target Market(s)

young generation

Coding

Coded - Design and coding required

Number of Pages Required

5+ page

Font styles to use
Sans Serif

Colors
0592cd
33a6d7
85cae6
00a990
33b8a4
86cfc6
cee9f5
cfeae6
3277b5

Requirements
Must have
• *Should be able to switch from English to Chinese
Nice to have
• http://www.thebrightarchclinic.com/
• As a reference, the above link is the current website, but we would like to change the appearance and the content (our new logo's picture is attached)

```html
<!DOCTYPE html>
<html lang="en">
<head>
<meta charset="utf-8">
<title>The Bright Arch Clinic</title>
<link rel="stylesheet" href="https://fonts.googleapis.com/css2?family=Montserrat:wght@400;500;600;700&family=Arimo:wght@400;700&display=swap">
<style>
:root{
  --blue:#0592cd;
  --blue-mid:#2b8fd6;
  --blue-light:#85cae6;
  --blue-pale:#cee9f5;
  --green:#00a990;
  --green-mid:#33b8a4;
  --deep:#3277b5;
  --ink:#222;
  --text:#444;
  --muted:#666;
  --footer:#2c2c2c;
}
*{margin:0;padding:0;box-sizing:border-box}
html,body{width:1200px;height:3740px;overflow:hidden;background:#fff}
body{position:relative;font-family:'Arimo',Arial,sans-serif;color:var(--text)}
.abs{position:absolute}
.head-font{font-family:'Montserrat',Arial,sans-serif}

/* header */
.brand{left:112px;top:30px;display:flex;align-items:center;gap:14px}
.brand-mark{width:50px;height:50px;background:var(--blue-mid);border-radius:6px}
.brand-name{font-family:'Montserrat',sans-serif;font-weight:700;color:var(--blue-mid);font-size:24px;line-height:26px;letter-spacing:.5px}
.call{left:663px;top:30px;display:flex;align-items:center;gap:12px}
.call-icon{width:54px;height:54px;border:2px solid var(--blue-mid);border-radius:50%;display:flex;align-items:center;justify-content:center}
.call-text{font-family:'Montserrat',sans-serif;font-size:20px;font-weight:500;color:var(--ink)}
.lang{left:972px;top:35px;width:117px;height:39px;border:1px solid #bbb;display:flex;align-items:center;padding:0 8px;gap:6px;font-size:13px;color:#333}
.lang-flag{width:22px;height:14px;background:#1e3f8a;border:1px solid #c33}
.lang-caret{margin-left:auto;width:0;height:0;border-left:5px solid transparent;border-right:5px solid transparent;border-top:5px solid #333}

/* nav */
.nav{left:0;top:113px;width:1200px;height:61px;background:var(--blue-mid)}
.nav a{position:absolute;top:0;height:61px;line-height:61px;color:#fff;font-family:'Montserrat',sans-serif;font-size:12px;font-weight:600;text-decoration:none;transform:translateX(-50%);white-space:nowrap}
.nav .active{left:112px;width:136px;transform:none;text-align:center;background:#1a9b7e}

/* hero */
.hero{left:0;top:174px;width:1200px;height:766px;background:linear-gradient(100deg,#cfe3e6 0%,#dceff2 35%,#c9a98e 60%,#e8dccf 80%,#d6ebf2 100%)}
.hero-curve{left:0;top:820px;width:1200px;height:125px}
.hero-title{left:112px;top:352px;font-size:50px;font-weight:600;color:var(--blue-mid)}
.hero-sub{left:112px;top:432px;font-size:18px;line-height:34px;color:#333;font-weight:500}
.btn{display:inline-block;background:var(--blue-mid);color:#fff;font-family:'Montserrat',sans-serif;font-weight:600;text-align:center;border-radius:2px}
.hero-btn{left:112px;top:527px;width:215px;height:52px;line-height:52px;font-size:14px}
.dots{left:576px;top:798px;display:flex;gap:7px}
.dots span{width:11px;height:11px;border-radius:50%;background:#222}
.dots .on{background:var(--green)}

/* welcome */
.center{left:0;width:1200px;text-align:center}
.w-small{top:880px;font-size:20px;font-weight:500;color:var(--ink)}
.w-big{top:910px;font-size:30px;font-weight:600;color:var(--blue-mid)}
.smile{left:522px;width:156px;height:36px}
.w-text{top:1020px;font-size:13.5px;line-height:35px;color:var(--text)}

/* features */
.feature{top:1167px;width:325px;height:331px;text-align:center}
.feature.raised{background:#fff;box-shadow:0 0 18px rgba(0,0,0,.12)}
.feature svg{margin-top:34px}
.feature h3{font-family:'Montserrat',sans-serif;font-weight:500;font-size:16px;color:var(--ink);margin-top:20px}
.feature p{font-size:12.5px;line-height:27px;color:var(--text);margin:12px 28px 0}

/* offer */
.offer{left:0;top:1583px;width:1200px;height:571px;background:linear-gradient(90deg,#f1eeec 0%,#ece8e6 40%,#d7c7bf 62%,#cfb7aa 80%,#e2d8d2 100%)}
.sec-title{font-family:'Montserrat',sans-serif;font-weight:600;font-size:30px;color:var(--blue-mid)}
.offer-title{left:129px;top:1655px}
.offer-text{left:129px;top:1718px;width:460px;font-size:13.5px;line-height:28px}
.checks{left:129px;top:1830px;list-style:none;font-size:13.5px}
.checks li{height:51.5px;display:flex;align-items:flex-start;gap:22px}
.offer-btn{left:130px;top:2045px;width:147px;height:49px;line-height:49px;font-size:14px}

/* portal */
.portal{left:0;top:2154px;width:1200px;height:454px;background:linear-gradient(90deg,#fff 0%,#f6f8f9 40%,#eef1f2 70%,#e3e6e7 100%)}
.portal-ring{left:167px;top:2225px;width:316px;height:316px;border:4px solid #b9dff1;border-radius:50%;background:#fff;display:flex;align-items:center;justify-content:center;gap:10px}
.partner-dot{width:22px;height:22px;border-radius:50%;background:#0b6b4f}
.partner-name{font-family:'Montserrat',sans-serif;font-weight:600;font-size:34px;color:#0b6b4f}
.portal-title{left:541px;top:2283px}
.portal-text{left:541px;top:2346px;width:497px;font-size:12.5px;line-height:29.3px;color:var(--text)}
.portal-text a{color:var(--blue-mid);text-decoration:none}

/* reviews */
.reviews{left:0;top:2608px;width:1200px;height:496px;background:linear-gradient(90deg,#1a9b8a 0%,#1f8fb0 50%,#2680c2 100%)}
.rev-title{top:2656px;font-family:'Montserrat',sans-serif;font-weight:500;font-size:32px;color:#fff}
.review{top:2774px;width:380px;text-align:center;color:#fff}
.quote{width:92px;height:92px;border:2px solid #fff;border-radius:50%;margin:0 auto;display:flex;align-items:center;justify-content:center;font-family:'Montserrat',sans-serif;font-weight:700;font-size:44px;line-height:1;padding-top:18px}
.stars{margin-top:12px;font-size:13px;letter-spacing:3px}
.review h4{font-family:'Montserrat',sans-serif;font-weight:500;font-size:15px;margin-top:6px}
.review p{font-size:12px;line-height:27.5px;margin-top:12px}
.arrow{top:2885px}

/* contact */
.ct-title{top:3148px;font-family:'Montserrat',sans-serif;font-weight:600;font-size:32px;color:var(--blue-mid)}
.map{left:155px;top:3273px;width:440px;height:329px;background:linear-gradient(135deg,#e9e9e6,#dcdcd8);border:4px solid #fff;box-shadow:0 0 8px rgba(0,0,0,.25)}
.addr{left:638px;top:3278px;font-size:12.5px;line-height:25px;color:#333}
.field{border:1px solid #ccc;box-shadow:inset 0 0 3px rgba(0,0,0,.1);font-size:11px;color:#555;padding:14px 16px}
.submit{left:640px;top:3550px;width:125px;height:44px;line-height:44px;font-size:14px}

/* footer */
.footer{left:0;top:3672px;width:1200px;height:68px;background:var(--footer);color:#fff;text-align:center;line-height:68px;font-size:13px;font-family:'Montserrat',sans-serif}
</style>
</head>
<body>

<header>
  <div class="abs brand">
    <div class="brand-mark"></div>
    <div class="brand-name">THE BRIGHT ARCH<br>CLINIC</div>
  </div>
  <div class="abs call">
    <div class="call-icon">
      <svg width="18" height="18" viewBox="0 0 24 24"><path fill="#2b8fd6" d="M6.6 10.8a15.1 15.1 0 0 0 6.6 6.6l2.2-2.2a1 1 0 0 1 1-.25 11.4 11.4 0 0 0 3.6.57 1 1 0 0 1 1 1V20a1 1 0 0 1-1 1A17 17 0 0 1 3 4a1 1 0 0 1 1-1h3.5a1 1 0 0 1 1 1c0 1.25.2 2.45.57 3.57a1 1 0 0 1-.25 1z"/></svg>
    </div>
    <div class="call-text">CALL US: 617.555.0142</div>
  </div>
  <div class="abs lang"><span class="lang-flag"></span>English<span class="lang-caret"></span></div>
</header>

<nav class="abs nav">
  <a class="active">HOME</a>
  <a style="left:300px">MEET US</a>
  <a style="left:431px">SERVICES</a>
  <a style="left:576px">PATIENT INFO</a>
  <a style="left:743px">CASES&amp;REVIEWS</a>
  <a style="left:886px">BLOG</a>
  <a style="left:1005px">CONTACT</a>
</nav>

<section>
  <div class="abs hero" role="img" aria-label="Photo of a smiling young woman resting her head on her hands"></div>
  <svg class="abs hero-curve" viewBox="0 0 1200 125" preserveAspectRatio="none"><path d="M0 120 Q600 -110 1200 120 L1200 125 L0 125Z" fill="#fff"/></svg>
  <h1 class="abs hero-title head-font">The Bright Arch Clinic</h1>
  <p class="abs hero-sub head-font">Sed ut perspiciatis unde omnis iste natus error sit<br>voluptatem accusantium dolorem</p>
  <span class="abs btn hero-btn">REQUEST APPOINTMENT</span>
  <div class="abs dots"><span></span><span class="on"></span><span></span></div>
</section>

<section>
  <div class="abs center w-small head-font">WELCOME TO</div>
  <div class="abs center w-big head-font">THE BRIGHT ARCH CLINIC</div>
  <svg class="abs smile" style="top:958px" viewBox="0 0 156 36"><path d="M8 8 Q78 52 148 8" fill="none" stroke="#2b8fd6" stroke-width="5" stroke-linecap="round"/><circle cx="8" cy="8" r="7" fill="#2b8fd6"/><circle cx="148" cy="8" r="7" fill="#2b8fd6"/></svg>
  <p class="abs center w-text">Welcome to The Bright Arch Clinic where we specialize in General and Cosmetic Dentistry, Dental Implants,<br>Periodontics (Gum Surgery), Endodontics (Root Canal Treatment) and Reconstructive Dentistry for patients in<br>all other surrounding neighborhoods of Linwood, Massachusetts.</p>

  <div class="abs feature" style="left:109px">
    <svg width="109" height="122" viewBox="0 0 109 122"><path d="M0 6a6 6 0 0 1 6-6h97a6 6 0 0 1 6 6v116Q54.5 82 0 122Z" fill="#2b8fd6"/><path d="M34 30c8-6 16-2 20 1 4-3 12-7 20-1 8 7 2 24-2 32-3 8-3 20-8 20-5 0-4-16-10-16s-5 16-10 16c-5 0-5-12-8-20-4-8-10-25-2-32z" fill="none" stroke="#fff" stroke-width="4"/></svg>
    <h3>COSMETIC DENTISTRY</h3>
    <p>Sed ut perspiciatis unde omnis iste natus error sit voluptatem accusantium doloremque laudantium, totam rem aperiam</p>
  </div>
  <div class="abs feature raised" style="left:437px">
    <svg width="109" height="122" viewBox="0 0 109 122"><path d="M0 6a6 6 0 0 1 6-6h97a6 6 0 0 1 6 6v116Q54.5 82 0 122Z" fill="#1a9b7e"/><rect x="24" y="30" width="61" height="42" rx="14" fill="none" stroke="#fff" stroke-width="4"/><line x1="24" y1="51" x2="85" y2="51" stroke="#fff" stroke-width="3"/><line x1="40" y1="32" x2="40" y2="70" stroke="#fff" stroke-width="3"/><line x1="54.5" y1="32" x2="54.5" y2="70" stroke="#fff" stroke-width="3"/><line x1="69" y1="32" x2="69" y2="70" stroke="#fff" stroke-width="3"/></svg>
    <h3>GENERAL DENTISTRY</h3>
    <p>Sed ut perspiciatis unde omnis iste natus error sit voluptatem accusantium doloremque laudantium, totam rem aperiam</p>
  </div>
  <div class="abs feature" style="left:761px">
    <svg width="109" height="122" viewBox="0 0 109 122"><path d="M0 6a6 6 0 0 1 6-6h97a6 6 0 0 1 6 6v116Q54.5 82 0 122Z" fill="#2b8fd6"/><circle cx="45" cy="34" r="11" fill="none" stroke="#fff" stroke-width="4"/><path d="M24 82c0-16 9-26 21-26s21 10 21 26" fill="none" stroke="#fff" stroke-width="4"/><path d="M68 60c4-3 8-1 9 0 2-1 6-3 9 0 3 4 0 11-1 15-1 4-2 8-4 8s-2-7-4-7-2 7-4 7-2-5-3-8c-2-4-4-11-2-15z" fill="none" stroke="#fff" stroke-width="3"/></svg>
    <h3>MULTI-SPECIALTY DENTAL CARE</h3>
    <p>Sed ut perspiciatis unde omnis iste natus error sit voluptatem accusantium doloremque laudantium, totam rem aperiam</p>
  </div>
</section>

<section>
  <div class="abs offer" role="img" aria-label="Photo of a dentist examining a smiling patient with a dental mirror"></div>
  <h2 class="abs sec-title offer-title">NEW PATIENT OFFER</h2>
  <p class="abs offer-text">Sed ut perspiciatis unde omnis iste natus error sit voluptatem accusantium doloremque laudantium, totam rem aperiam, eaque ipsa quae ab illo invet asi architecto beatae vitae dicta sunt explicabo.</p>
  <ul class="abs checks">
    <li><svg width="14" height="12" viewBox="0 0 14 12"><path d="M1 6l4 4 8-9" fill="none" stroke="#2b8fd6" stroke-width="3"/></svg>Sed ut perspiciatis unde omnis iste natus error sit</li>
    <li><svg width="14" height="12" viewBox="0 0 14 12"><path d="M1 6l4 4 8-9" fill="none" stroke="#2b8fd6" stroke-width="3"/></svg>Voluptatem accusantium doloremque laudantium</li>
    <li><svg width="14" height="12" viewBox="0 0 14 12"><path d="M1 6l4 4 8-9" fill="none" stroke="#2b8fd6" stroke-width="3"/></svg>Totam rem aperiam, eaque ipsa quae ab</li>
    <li><svg width="14" height="12" viewBox="0 0 14 12"><path d="M1 6l4 4 8-9" fill="none" stroke="#2b8fd6" stroke-width="3"/></svg>Asi architecto beatae vitae dicta sunt explicabo</li>
  </ul>
  <span class="abs btn offer-btn">VIEW OFFER</span>
</section>

<section>
  <div class="abs portal" role="img" aria-label="Faded photo of a smiling woman"></div>
  <div class="abs portal-ring"><span class="partner-dot"></span><span class="partner-name">FlexCare Pay</span></div>
  <h2 class="abs sec-title portal-title">PATIENT PORTAL</h2>
  <p class="abs portal-text">Thank you for your trust in us. We look forward to working with you towards a healthy and beautiful smile. Prior to your first appointment, we request that you please download and complete The New Patient Form – <a>Adults or The New Patient Form – Children (16 &amp; Under)</a>.We accept most insurance and all major credit cards. We also offer special finance option through FlexCare Pay.</p>
</section>

<section>
  <div class="abs reviews" role="img" aria-label="Teal and blue tinted photo of a smile"></div>
  <h2 class="abs center rev-title">CASES &amp; REVIEWS</h2>
  <svg class="abs smile" style="top:2708px;left:543px;width:114px;height:28px" viewBox="0 0 114 28"><path d="M6 6 Q57 40 108 6" fill="none" stroke="#fff" stroke-width="4" stroke-linecap="round"/><circle cx="6" cy="6" r="5" fill="#fff"/><circle cx="108" cy="6" r="5" fill="#fff"/></svg>
  <svg class="abs arrow" style="left:64px" width="20" height="96" viewBox="0 0 20 96"><path d="M18 2 L2 48 L18 94" fill="none" stroke="#fff" stroke-width="1.5"/></svg>
  <svg class="abs arrow" style="left:1128px" width="20" height="96" viewBox="0 0 20 96"><path d="M2 2 L18 48 L2 94" fill="none" stroke="#fff" stroke-width="1.5"/></svg>
  <div class="abs review" style="left:150px">
    <div class="quote">”</div>
    <div class="stars">★★★★★</div>
    <h4>PRIYA NANDAL</h4>
    <p>I have been coming to this facility for a year and I must say that this has been the best dental office that I have ever been to. have always had issues going to a dental office due my fears from chil dhood but Dr.Varden makes me feel comfortable</p>
  </div>
  <div class="abs review" style="left:663px">
    <div class="quote">”</div>
    <div class="stars">★★★★★</div>
    <h4>MARLA WHITFIELD</h4>
    <p>I LOVE everyone at this office!! Dr. Varden is the best of the best. The office staff are always courteous and kind, even kept an eye on my granddaughter who was watching TV while I was being every office strives to be--they have it all!!</p>
  </div>
</section>

<section>
  <h2 class="abs center ct-title">CONTACT US</h2>
  <svg class="abs smile" style="top:3198px;left:539px;width:122px;height:30px" viewBox="0 0 122 30"><path d="M6 6 Q61 42 116 6" fill="none" stroke="#2b8fd6" stroke-width="4" stroke-linecap="round"/><circle cx="6" cy="6" r="5" fill="#2b8fd6"/><circle cx="116" cy="6" r="5" fill="#2b8fd6"/></svg>
  <div class="abs map" role="img" aria-label="Street map showing the clinic location"></div>
  <div class="abs addr">Address : # 2210 Harbor Lane Suite 305<br>Linwood, MA 02446<br><span style="display:block;margin-top:10px">Phone : 1-617-555-0142 &nbsp;/ &nbsp;Email: info@thebrightarchclinic.com</span></div>
  <div class="abs field" style="left:640px;top:3382px;width:178px;height:42px">Name :</div>
  <div class="abs field" style="left:640px;top:3432px;width:178px;height:42px">Email :</div>
  <div class="abs field" style="left:640px;top:3482px;width:178px;height:42px">Phone :</div>
  <div class="abs field" style="left:825px;top:3382px;width:221px;height:142px">Message :</div>
  <span class="abs btn submit">SUBMIT</span>
</section>

<footer class="abs footer">© Copyright-2019 The Bright Arch Clinic. All rights reserved.</footer>

</body>
</html>
```